Modern Business Card

Modern professional business card with more than just logo and demographic info. Something memorable.

We are a trendy/modern chiropractic group with an emphasis on neurology, hence the minimalist-type brain logo. We want to convey that modern and technical aspect with professionalism and the elite nature of our practice environment.

```html
<!DOCTYPE html>
<html lang="en">
<head>
<meta charset="utf-8">
<title>Northline Chiropractic – Business Card</title>
<link rel="stylesheet" href="https://fonts.googleapis.com/css2?family=Roboto+Slab:wght@400;700&display=swap">
<style>
  :root {
    --page: #e6e7e9;
    --card-black: #0f0f10;
    --card-white: #ffffff;
    --brand-blue: #447fc1;
    --ink: #1c1c1c;
    --silver: #8d8f93;
    --divider: #b9bcc1;
  }
  * { box-sizing: border-box; margin: 0; padding: 0; }
  html, body {
    width: 1200px; height: 1015px; overflow: hidden;
    background: var(--page);
    font-family: "Roboto Slab", Georgia, serif;
  }
  .canvas {
    width: 1200px; height: 1015px;
    display: flex; flex-direction: column; align-items: center; justify-content: center;
    gap: 60px;
  }
  .card {
    width: 630px; height: 360px; position: relative; overflow: hidden;
    box-shadow: 0 6px 18px rgba(0,0,0,.18);
  }
  /* Front */
  .card-front {
    background: var(--card-black);
    border-bottom: 10px solid var(--brand-blue);
    display: flex; align-items: center; justify-content: center;
  }
  .wordmark {
    display: flex; align-items: center; gap: 16px;
    font-weight: 400; letter-spacing: 2px; text-transform: uppercase;
  }
  .wordmark-mark { width: 46px; height: 46px; }
  .card-front .wordmark { color: var(--silver); font-size: 30px; }
  .card-front .wordmark-mark { background: var(--silver); }
  /* Back */
  .card-back { background: var(--card-white); }
  .back-body {
    position: absolute; left: 0; top: 0; width: 100%; height: 245px;
    display: flex; align-items: center;
  }
  .back-brand {
    width: 300px; display: flex; justify-content: center;
  }
  .card-back .wordmark {
    flex-direction: column; gap: 12px; color: var(--ink); font-size: 22px; text-align: center;
  }
  .card-back .wordmark-mark { background: var(--brand-blue); width: 40px; height: 40px; }
  .divider { width: 1px; height: 130px; background: var(--divider); }
  .contact {
    padding-left: 24px; color: var(--ink); font-size: 15px; line-height: 1.5;
  }
  .contact-name {
    color: var(--brand-blue); font-weight: 700; font-size: 20px;
    text-transform: uppercase; line-height: 1.1;
  }
  .contact-role { font-size: 15px; margin-bottom: 8px; }
  .contact-line { display: flex; align-items: center; gap: 6px; }
  .contact-line svg { width: 16px; height: 16px; flex: none; }
  .contact-address { margin-top: 10px; }
  .back-band {
    position: absolute; left: 0; bottom: 0; width: 100%; height: 115px;
    background: var(--brand-blue);
    display: flex; align-items: center; justify-content: flex-end; padding-right: 70px;
  }
  .website { color: #fff; font-weight: 700; font-size: 20px; letter-spacing: .5px; }
</style>
</head>
<body>
<main class="canvas">
  <section class="card card-front" aria-label="Card front">
    <div class="wordmark"><span class="wordmark-mark"></span><span>Northline Chiropractic</span></div>
  </section>

  <section class="card card-back" aria-label="Card back">
    <div class="back-body">
      <div class="back-brand">
        <div class="wordmark"><span class="wordmark-mark"></span><span>Northline<br>Chiropractic</span></div>
      </div>
      <div class="divider"></div>
      <div class="contact">
        <p class="contact-name">Marcus Hale</p>
        <p class="contact-role">Managing Director</p>
        <p class="contact-line">
          <svg viewBox="0 0 16 16"><rect x="0.75" y="0.75" width="14.5" height="14.5" rx="2" fill="none" stroke="var(--brand-blue)" stroke-width="1.5"/><path d="M5 4 L6.5 4 L7.3 6 L6.3 7 Q7.3 9 9 9.7 L10 8.7 L12 9.5 L12 11 Q8 12 5.5 9 Q4 7 5 4 Z" fill="var(--brand-blue)"/></svg>
          044-555 010 234
        </p>
        <p class="contact-line">
          <svg viewBox="0 0 16 16"><rect x="0.5" y="3" width="15" height="10" fill="var(--brand-blue)"/><path d="M0.5 3 L8 9 L15.5 3" fill="none" stroke="#fff" stroke-width="1.2"/></svg>
          hello@northline.com
        </p>
        <p class="contact-address">88, Harbour Lane<br>Westfield, 20418</p>
      </div>
    </div>
    <div class="back-band">
      <p class="website">www.northlinechiro.com</p>
    </div>
  </section>
</main>
</body>
</html>
```